Brookvane Consulting Business Card Design

Business Card Design for Brookvane Consulting. Brookvane Consulting is a boutique consultancy based in Atlanta, GA., that specializes in marketing strategy, organization planning, and leadership development. We provide solutions for small businesses and startups as well as Vantage 300 companies.

http://brookvaneconsulting.com/

Target Market(s)

We provide solutions for small businesses and startups as well as Vantage 300 companies.

Industry/Entity Type

Consulting

Contact Information for Business Card

Two sided business card with priority on contact information, logo, tag line (Inspiration to Dream More, Do More, Become More)

Colors

Designer to choose colors to be used in the design.

Requirements
Must have
• contact information, logo, tag line (Inspiration to Dream More, Do More, Become More)
• Simple no over communication.
Nice to have
• I would like to see different placements of logo and creative use of both sides of the card
Should not have
• Do not put too much information on the card.

```html
<!DOCTYPE html>
<html lang="en">
<head>
<meta charset="utf-8">
<title>Brookvane Consulting Business Card</title>
<link rel="stylesheet" href="https://fonts.googleapis.com/css2?family=Roboto:wght@400;500&display=swap">
<style>
  :root {
    --backdrop: #3b3b3b;
    --card-dark: #2e2e2e;
    --card-light: #f1f1f1;
    --ink-dark: #1f1f1f;
    --ink-mid: #3a3a3a;
    --ink-on-dark: #cfcfcf;
    --white: #ffffff;
  }
  * { margin: 0; padding: 0; box-sizing: border-box; }
  html, body {
    width: 799px; height: 1200px; overflow: hidden;
    background: var(--backdrop);
    font-family: "Roboto", Arial, sans-serif;
  }
  .canvas { position: relative; width: 799px; height: 1200px; }
  .card {
    position: absolute; left: 90px;
    width: 620px; height: 354px;
    border-radius: 22px; overflow: hidden;
    box-shadow: 0 14px 30px rgba(0,0,0,0.45);
  }
  .card-front { top: 150px; background: var(--card-dark); }
  .card-back { top: 690px; background: var(--card-light); }

  .brand-name {
    font-family: "Roboto", Arial, sans-serif;
    font-weight: 500;
    letter-spacing: 0.02em;
  }
  .card-front .brand-name {
    position: absolute; left: 0; right: 0; top: 150px;
    text-align: center; font-size: 40px;
    color: var(--ink-on-dark);
  }
  .card-back .brand-name {
    position: absolute; left: 60px; top: 52px;
    font-size: 30px; color: var(--ink-dark);
  }

  .contact {
    position: absolute; left: 60px; top: 128px;
    color: var(--ink-dark);
  }
  .contact-name { font-size: 20px; font-weight: 500; margin-bottom: 10px; }
  .contact-line { font-size: 14px; line-height: 19px; color: var(--ink-mid); }

  .wave { position: absolute; left: 0; top: 0; width: 620px; height: 354px; }

  .tagline {
    position: absolute; right: 32px; bottom: 18px;
    text-align: right; color: var(--white);
    font-size: 15px; line-height: 19px;
  }
</style>
</head>
<body>
<main class="canvas">
  <section class="card card-front" aria-label="Card front">
    <p class="brand-name">Brookvane Consulting</p>
  </section>

  <section class="card card-back" aria-label="Card back">
    <svg class="wave" viewBox="0 0 620 354" aria-hidden="true">
      <path d="M0 232 C120 270, 260 276, 360 266 C460 254, 540 210, 620 160 L620 174 C540 224, 460 268, 360 280 C260 290, 120 284, 0 246 Z" fill="#2e2e2e"/>
      <path d="M0 262 C120 300, 260 306, 360 296 C460 280, 540 236, 620 186 L620 354 L0 354 Z" fill="#2e2e2e"/>
    </svg>
    <p class="brand-name">Brookvane Consulting</p>
    <div class="contact">
      <p class="contact-name">Tavian</p>
      <p class="contact-line">555-014-2290</p>
      <p class="contact-line">tavian@brookvaneconsulting.com</p>
      <p class="contact-line">www.brookvaneconsulting.com</p>
    </div>
    <p class="tagline">Inspiration to<br>Dream More,<br>Do More,<br>Become More</p>
  </section>
</main>
</body>
</html>
```